Letterhead & Greeting Card Design Project

I need a few files prepared for dynamic digital printing: letterhead and 2 postcards with an envelope for each. Enclosed are specific directions from the printer for each file and overall. I have also enclosed mockups of what I would like on those designs and some raw files to work with.

Industry/Entity Type

Digital

```html
<!DOCTYPE html>
<html lang="en">
<head>
<meta charset="utf-8">
<title>Cadence Media — Letterhead</title>
<link rel="stylesheet" href="https://fonts.googleapis.com/css2?family=Ubuntu:wght@400;500&family=Arimo&display=swap">
<style>
  :root {
    --paper: #ffffff;
    --ink: #3f3f3f;
    --ink-soft: #555555;
    --brand-grey: #5a5a5a;
    --brand-blue: #3aa7dc;
    --footer-grey: #8a8a8a;
  }
  * { margin: 0; padding: 0; box-sizing: border-box; }
  html, body { width: 933px; height: 1200px; overflow: hidden; background: var(--paper); }
  .letterhead {
    position: relative;
    width: 933px;
    height: 1200px;
    background: var(--paper);
    color: var(--ink);
    font-family: "Ubuntu", sans-serif;
    font-size: 17.5px;
    line-height: 29.5px;
  }
  .brand {
    position: absolute;
    top: 58px;
    left: 470px;
    display: flex;
    align-items: center;
    gap: 18px;
  }
  .brand-mark { width: 42px; height: 42px; }
  .brand-name {
    font-family: "Ubuntu", sans-serif;
    font-weight: 500;
    font-size: 58px;
    line-height: 1;
    color: var(--brand-grey);
    letter-spacing: -0.5px;
  }
  .letter {
    position: absolute;
    left: 117px;
    top: 156px;
    width: 790px;
  }
  .letter-date { margin-bottom: 30px; }
  .recipient { margin-bottom: 46px; color: var(--ink-soft); }
  .salutation { margin-bottom: 30px; }
  .letter-body p { margin-bottom: 30px; }
  .closing { margin-top: 44px; margin-bottom: 22px; }
  .sender { color: var(--ink-soft); }
  .footer-address {
    position: absolute;
    top: 1138px;
    left: 280px;
    font-family: "Arimo", sans-serif;
    font-size: 18px;
    color: var(--footer-grey);
    letter-spacing: 0.2px;
  }
</style>
</head>
<body>
<main class="letterhead">
  <header class="brand">
    <svg class="brand-mark" viewBox="0 0 42 42" aria-hidden="true"><circle cx="21" cy="21" r="18" fill="var(--brand-blue)"/></svg>
    <span class="brand-name">Cadence Media</span>
  </header>

  <section class="letter">
    <p class="letter-date">November 08, 2012</p>

    <address class="recipient" style="font-style: normal;">
      John Doe<br>
      Account Name<br>
      Address 1<br>
      Address 2
    </address>

    <p class="salutation">Dear Customer:</p>

    <div class="letter-body">
      <p>Lorem ipsum dolor sit amet, consectetur adipiscing elit. Donec elementum velit sit amet libero fringilla adipiscing. Aliquam sollicitudin, leo vitae molestie facilisis, tellus ligula varius velit, vitae tincidunt lacus purus vitae nulla. Nulla imperdiet, odio quis ultrices ornare, diam est dictum lacus, et vehicula est magna at metus. Integer mattis lorem quis tortor accumsan ultrices ac ut massa. Duis eget metus ut risus scelerisque ornare quis eget dui. Aliquam lobortis dolor vitae magna volutpat eu facilisis tellus molestie. Sed a purus quis nibh lacinia interdum ut at leo. Sed sem dui, mollis in pellentesque sed, placerat non erat. Cum sociis natoque penatibus et magnis dis parturient montes, nascetur ridiculus mus. In lacinia arcu non felis laoreet sed convallis lectus tincidunt. Duis quis mauris et enim egestas molestie vel id sem.</p>
      <p>Integer consequat velit quis elit hendrerit imperdiet. Donec felis velit, volutpat vel convallis nec, sollicitudin et nulla. Pellentesque sodales elementum aliquam. Donec convallis, turpis sit amet laoreet ultricies, enim est elementum magna, dictum lobortis eros tellus quis diam. Nunc suscipit augue non nisl volutpat volutpat. Ut egestas ultrices purus, eget varius nibh placerat in. Cras leo ante, congue id ultricies a, ornare eu est. Curabitur eleifend tincidunt mi eget tristique.</p>
    </div>

    <p class="closing">Thanking you,</p>

    <p class="sender">
      John Doe<br>
      Company<br>
      Phone<br>
      Email
    </p>
  </section>

  <footer class="footer-address">Street • City • State/Providence • Zip/Postal Code</footer>
</main>
</body>
</html>
```